World Wide News and Current Affairs website

We intends to start up a new website which deals on New and Current Affairs.
Attention Designers,
We want a home page design for this project. Our business is based in the United States. Our goal is to become a well known brand.
The website would consist of a category for News, Business and Tech.
The theme should be beautiful and attention seeking. The website would take bulk of it's news from the US, and Europe.
Designers can get inspiration from already existing new websites such as PWJ, KLV, DASKOLM.
All designs should be clean and easy to navigate.

```html
<!DOCTYPE html>
<html lang="en">
<head>
<meta charset="utf-8">
<title>Harlow News</title>
<link href="https://fonts.googleapis.com/css2?family=Open+Sans:wght@400;600;700&display=swap" rel="stylesheet">
<style>
:root{
  --dark:#333333;
  --darker:#2b2b2b;
  --ink:#1e1e1e;
  --muted:#8a8a8a;
  --line:#dddddd;
  --tint:#f2f2f2;
  --white:#ffffff;
  --link:#3a7bc8;
}
*{box-sizing:border-box;margin:0;padding:0}
html,body{width:1200px;height:3226px;overflow:hidden}
body{font-family:"Open Sans",Arial,sans-serif;color:var(--ink);background:var(--white)}
.wrap{width:936px;margin:0 auto;position:relative}
.ph{display:block;position:relative}
.play{position:absolute;left:50%;top:50%;transform:translate(-50%,-50%)}

/* header */
.site-header{height:80px;background:var(--dark)}
.site-header .wrap{display:flex;align-items:center;height:80px}
.brand{font-size:33px;font-weight:600;color:var(--white);letter-spacing:-.3px}
.nav{margin-left:auto;display:flex;align-items:center;gap:26px;font-size:12px;color:#c9c9c9}
.nav .active{color:var(--white);text-decoration:underline;text-underline-offset:4px}
.nav .sep{width:1px;height:28px;background:#555;margin:0 4px}

/* hero */
.hero{display:flex;gap:10px;margin-top:17px;height:303px}
.hero-main{width:465px;height:303px;background:linear-gradient(120deg,#e9e6e1,#cfd3d8 55%,#f4f4f2)}
.hero-cap{position:absolute;left:18px;right:0;bottom:0;height:66px;background:rgba(40,40,40,.82);padding:10px 16px;color:var(--white)}
.hero-cap h2{font-size:19px;font-weight:700}
.hero-cap p{font-size:11px;color:#ddd;margin-top:3px}
.hero-videos{width:226px;display:flex;flex-direction:column;gap:13px}
.hero-videos .ph{height:145px}
.v1{background:linear-gradient(135deg,#9c8d78,#cbbfa9 60%,#6f655a)}
.v2{background:linear-gradient(135deg,#4c4f55,#8d8a84 60%,#3a3c40)}
.side-list{margin-left:7px;width:218px;border:1px solid var(--line);font-size:10px;color:#444}
.side-list h3{font-size:15px;font-weight:600;padding:8px 12px;border-bottom:1px solid var(--line)}
.side-list li{list-style:none;padding:7px 12px;border-bottom:1px solid var(--line);line-height:1.35;height:47px}
.side-list .all{padding:9px 12px;font-size:10px}

/* ad */
.ad{width:580px;height:71px;margin:17px auto 0;display:flex;border:1px solid #e8e8e8}
.ad .ph{width:335px;background:linear-gradient(90deg,#dfe6ee,#b8c3cf 50%,#e9edf1)}
.ad-text{padding:10px 0 0 30px;color:var(--link);font-size:14px;line-height:1.15}
.ad-text small{display:block;font-size:9px;color:var(--muted);margin-top:2px}

/* sections */
.section{position:relative}
.section.tint{background:var(--tint)}
.sec-head{display:flex;align-items:center;justify-content:space-between;height:26px}
.sec-head h2{font-size:20px;font-weight:700;text-transform:uppercase}
.view-all{background:var(--ink);color:var(--white);font-size:8px;font-weight:700;padding:3px 7px;text-transform:uppercase}
.cards{display:flex;gap:22px;margin-top:13px}
.card{width:297px}
.card .ph{height:191px}
.card h3{font-size:15.5px;font-weight:700;line-height:1.25;margin-top:10px}
.excerpt{font-size:10px;color:var(--muted);line-height:1.6;margin-top:6px}
.feature{display:flex;gap:6px;margin-top:38px;height:280px}
.feature .big{width:465px;height:280px}
.minis{flex:1;display:flex;flex-direction:column;gap:8px}
.mini{display:flex;height:136px;background:var(--tint)}
.tint .mini{background:var(--white)}
.mini .ph{width:161px;height:136px;flex:none}
.mini div{padding:18px 18px}
.mini h3{font-size:15.5px;font-weight:700;line-height:1.25}

/* photo tones */
.t1{background:linear-gradient(135deg,#b08b5e,#d9c3a0 55%,#7d6648)}
.t2{background:linear-gradient(135deg,#6d6a66,#a9a39b 55%,#48433e)}
.t3{background:linear-gradient(135deg,#7a6a60,#b9aaa0 55%,#5b4f49)}
.t4{background:linear-gradient(135deg,#cfd4da,#9aa2ab 55%,#e8e9ea)}
.t5{background:linear-gradient(135deg,#b9d2dc,#e6eff2 55%,#8eaab6)}
.t6{background:linear-gradient(135deg,#6b4a36,#a3806a 55%,#3f2c22)}
.t7{background:linear-gradient(135deg,#8a6a4a,#c4a988 55%,#5d4532)}
.t8{background:linear-gradient(135deg,#c9ced3,#8b949c 55%,#eef0f1)}
.t9{background:linear-gradient(135deg,#e1e4e6,#a8b0b6 55%,#f4f5f5)}
.t10{background:linear-gradient(135deg,#a8a8a8,#dcdcdc 55%,#7a7a7a)}
.t11{background:linear-gradient(135deg,#b5a58f,#e3d9c9 55%,#8d7e6a)}
.t12{background:linear-gradient(135deg,#a3a19a,#d6d2c8 50%,#6f5f56)}
.t13{background:linear-gradient(135deg,#8fa7c0,#d4dde6 55%,#4c6684)}
.t14{background:linear-gradient(135deg,#3a4350,#6d7e90 55%,#232a33)}
.t15{background:radial-gradient(circle at 55% 55%,#bfe6f5,#4d8fb0 45%,#1e2d3a)}
.t16{background:linear-gradient(135deg,#5e6b75,#b4bcc2 55%,#3a3f44)}
.t17{background:linear-gradient(135deg,#7b6d63,#bfb3a9 55%,#4b413b)}
.t18{background:linear-gradient(135deg,#4a4a4a,#9a9a9a 55%,#2f2f2f)}

/* newsletter */
.newsletter{height:64px;background:var(--dark)}
.newsletter .wrap{display:flex;align-items:center;justify-content:center;height:64px;gap:10px}
.newsletter h2{font-size:19px;font-weight:700;color:var(--white);text-transform:uppercase;display:flex;align-items:center;gap:8px}
.nl-form{display:flex;margin-left:6px}
.nl-input{width:225px;height:36px;background:var(--white);font-size:10px;color:#777;padding:11px 14px}
.nl-btn{width:88px;height:36px;background:#555;color:var(--white);font-size:9px;text-transform:uppercase;text-align:center;line-height:36px}

/* footer */
.footer-cols{display:flex;padding-top:37px;height:224px}
.fcol{width:208px}
.fcol:last-child{width:auto}
.fcol h4{font-size:14px;font-weight:400;margin-bottom:9px}
.fcol li{list-style:none;font-size:10.5px;color:#555;line-height:20.5px}
.fcol li::before{content:"";display:inline-block;width:3px;height:3px;border-radius:50%;background:#555;margin:0 8px 2px 2px}
.footer-bottom{border-top:1px solid var(--line)}
.footer-bottom .wrap{display:flex;align-items:center;height:72px;font-size:10px;color:#555}
.social{margin-left:auto;display:flex;gap:6px}
.social span{width:24px;height:24px;border-radius:50%;background:#5a6472}
</style>
</head>
<body>

<header class="site-header">
  <div class="wrap">
    <div class="brand">Harlow News</div>
    <nav class="nav">
      <span class="active">News</span><span>Business</span><span>Tech</span><span>More &#9662;</span>
      <span class="sep"></span>
      <svg width="16" height="16" viewBox="0 0 16 16"><circle cx="6.5" cy="6.5" r="5" fill="none" stroke="#fff" stroke-width="2"/><line x1="10" y1="10" x2="15" y2="15" stroke="#fff" stroke-width="2.4"/></svg>
    </nav>
  </div>
</header>

<main>
<div class="wrap">
  <section class="hero">
    <div class="ph hero-main" role="img" aria-label="Man working at a laptop in a bright office">
      <div class="hero-cap"><h2>Donec eu suscipit felis, quis vehicula velit</h2><p>Nam condimentum metus sed nulla finibus, at iaculis ante porta.</p></div>
    </div>
    <div class="hero-videos">
      <div class="ph v1" role="img" aria-label="Video still of colleagues talking in an office"><svg class="play" width="40" height="40" viewBox="0 0 40 40"><circle cx="20" cy="20" r="20" fill="#fff"/><path d="M16 12l12 8-12 8z" fill="#222"/></svg></div>
      <div class="ph v2" role="img" aria-label="Video still of a team meeting"><svg class="play" width="40" height="40" viewBox="0 0 40 40"><circle cx="20" cy="20" r="20" fill="#fff"/><path d="M16 12l12 8-12 8z" fill="#222"/></svg></div>
    </div>
    <aside class="side-list">
      <h3>Curabitur hendrerit</h3>
      <ul>
        <li>Proin faucibus, elit ac ornare rutrum</li>
        <li>Praesent nec tempus sapien, semper ultricies sem</li>
        <li>Curabitur mi velit, scelerisque sed mi et, eleifend ultricies ipsum</li>
        <li>Nulla commodo pretium tortor, nec iaculis tellus tempus id</li>
        <li>Sed commodo risus eu ex molestie, vitae congue diam consequat.</li>
      </ul>
      <div class="all">View All &#9656;</div>
    </aside>
  </section>

  <div class="ad">
    <div class="ph" role="img" aria-label="Illustration of interlocking gears"></div>
    <div class="ad-text">PELLENTESQUE VEL<br>DIGNISSIM<small>Read more</small></div>
  </div>
</div>

<!-- NEWS -->
<section class="section" style="height:767px;padding-top:47px">
  <div class="wrap">
    <div class="sec-head"><h2>News</h2><span class="view-all">View all</span></div>
    <div class="cards">
      <article class="card"><div class="ph t1" role="img" aria-label="Business handshake over documents"></div><h3>Duis a neque non ipsum sollicitudin scelerisque egestas ut mauris</h3><p class="excerpt">Proin faucibus, elit ac ornare rutrum, urna risus pretium ante, in iaculis metus sapien ac nisl. Mauris vitae mauris tristique, sagittis libero eget, bibendum ante.</p></article>
      <article class="card"><div class="ph t2" role="img" aria-label="Two colleagues talking in an office"></div><h3>Praesent nec tempus sapien, semper ultricies sem.</h3><p class="excerpt">Proin faucibus, elit ac ornare rutrum, urna risus pretium ante, in iaculis metus sapien ac nisl. Mauris vitae mauris tristique, sagittis libero eget, bibendum ante.</p></article>
      <article class="card"><div class="ph t3" role="img" aria-label="Group of people seated with devices"></div><h3>Vivamus semper ligula lorem, vel ornare metus</h3><p class="excerpt">Proin faucibus, elit ac ornare rutrum, urna risus pretium ante, in iaculis metus sapien ac nisl. Mauris vitae mauris tristique, sagittis libero eget, bibendum ante.</p></article>
    </div>
    <div class="feature">
      <div class="ph big t4" role="img" aria-label="Video still of two people at a laptop"><svg class="play" width="40" height="40" viewBox="0 0 40 40"><circle cx="20" cy="20" r="20" fill="#fff"/><path d="M16 12l12 8-12 8z" fill="#222"/></svg></div>
      <div class="minis">
        <div class="mini"><div class="ph t5" role="img" aria-label="Presenter at a whiteboard"></div><div><h3>Vivamus semper ligula lorem, vel ornare metus</h3><p class="excerpt">Proin faucibus, elit ac ornare rutrum, urna risus pretium ante, in iaculis metus sapien ac nisl. Mauris vitae mauris tristique, sagittis libero.</p></div></div>
        <div class="mini"><div class="ph t6" role="img" aria-label="Audience at a conference"></div><div><h3>Vivamus semper ligula lorem, vel ornare metus</h3><p class="excerpt">Proin faucibus, elit ac ornare rutrum, urna risus pretium ante, in iaculis metus sapien ac nisl. Mauris vitae mauris tristique, sagittis libero.</p></div></div>
      </div>
    </div>
  </div>
</section>

<!-- BUSINESS -->
<section class="section tint" style="height:805px;padding-top:76px">
  <div class="wrap">
    <div class="sec-head"><h2>Business</h2><span class="view-all">View all</span></div>
    <div class="cards">
      <article class="card"><div class="ph t7" role="img" aria-label="Team working around a wooden table"></div><h3>Duis a neque non ipsum sollicitudin scelerisque egestas ut mauris</h3><p class="excerpt">Proin faucibus, elit ac ornare rutrum, urna risus pretium ante, in iaculis metus sapien ac nisl. Mauris vitae mauris tristique, sagittis libero eget, bibendum ante.</p></article>
      <article class="card"><div class="ph t8" role="img" aria-label="Business meeting at a glass table"></div><h3>Praesent nec tempus sapien, semper ultricies sem.</h3><p class="excerpt">Proin faucibus, elit ac ornare rutrum, urna risus pretium ante, in iaculis metus sapien ac nisl. Mauris vitae mauris tristique, sagittis libero eget, bibendum ante.</p></article>
      <article class="card"><div class="ph t9" role="img" aria-label="Open plan office with staff"></div><h3>Vivamus semper ligula lorem, vel ornare metus</h3><p class="excerpt">Proin faucibus, elit ac ornare rutrum, urna risus pretium ante, in iaculis metus sapien ac nisl. Mauris vitae mauris tristique, sagittis libero eget, bibendum ante.</p></article>
    </div>
    <div class="feature" style="margin-top:65px">
      <div class="minis">
        <div class="mini"><div class="ph t10" role="img" aria-label="Businessman with a megaphone"></div><div><h3>Vivamus semper ligula lorem, vel ornare metus</h3><p class="excerpt">Proin faucibus, elit ac ornare rutrum, urna risus pretium ante, in iaculis metus sapien ac nisl. Mauris vitae mauris tristique, sagittis libero.</p></div></div>
        <div class="mini"><div class="ph t11" role="img" aria-label="Hands typing on a laptop"></div><div><h3>Vivamus semper ligula lorem, vel ornare metus</h3><p class="excerpt">Proin faucibus, elit ac ornare rutrum, urna risus pretium ante, in iaculis metus sapien ac nisl. Mauris vitae mauris tristique, sagittis libero.</p></div></div>
      </div>
      <div class="ph big t12" role="img" aria-label="Video still of a desk seen from above"><svg class="play" width="40" height="40" viewBox="0 0 40 40"><circle cx="20" cy="20" r="20" fill="#fff"/><path d="M16 12l12 8-12 8z" fill="#222"/></svg></div>
    </div>
  </div>
</section>

<!-- TECH -->
<section class="section" style="height:806px;padding-top:75px">
  <div class="wrap">
    <div class="sec-head"><h2>Tech</h2><span class="view-all">View all</span></div>
    <div class="cards">
      <article class="card"><div class="ph t13" role="img" aria-label="Two colleagues at a computer"></div><h3>Duis a neque non ipsum sollicitudin scelerisque egestas ut mauris</h3><p class="excerpt">Proin faucibus, elit ac ornare rutrum, urna risus pretium ante, in iaculis metus sapien ac nisl. Mauris vitae mauris tristique, sagittis libero eget, bibendum ante.</p></article>
      <article class="card"><div class="ph t14" role="img" aria-label="Hands using a phone over a keyboard"></div><h3>Praesent nec tempus sapien, semper ultricies sem.</h3><p class="excerpt">Proin faucibus, elit ac ornare rutrum, urna risus pretium ante, in iaculis metus sapien ac nisl. Mauris vitae mauris tristique, sagittis libero eget, bibendum ante.</p></article>
      <article class="card"><div class="ph t15" role="img" aria-label="Glowing digital interface touched by a hand"></div><h3>Vivamus semper ligula lorem, vel ornare metus</h3><p class="excerpt">Proin faucibus, elit ac ornare rutrum, urna risus pretium ante, in iaculis metus sapien ac nisl. Mauris vitae mauris tristique, sagittis libero eget, bibendum ante.</p></article>
    </div>
    <div class="feature" style="margin-top:65px">
      <div class="ph big t16" role="img" aria-label="Video still of a developer at a laptop"><svg class="play" width="40" height="40" viewBox="0 0 40 40"><circle cx="20" cy="20" r="20" fill="#fff"/><path d="M16 12l12 8-12 8z" fill="#222"/></svg></div>
      <div class="minis">
        <div class="mini"><div class="ph t17" role="img" aria-label="Colleagues reviewing a screen"></div><div><h3>Vivamus semper ligula lorem, vel ornare metus</h3><p class="excerpt">Proin faucibus, elit ac ornare rutrum, urna risus pretium ante, in iaculis metus sapien ac nisl. Mauris vitae mauris tristique, sagittis libero.</p></div></div>
        <div class="mini"><div class="ph t18" role="img" aria-label="Desk telephone close up"></div><div><h3>Vivamus semper ligula lorem, vel ornare metus</h3><p class="excerpt">Proin faucibus, elit ac ornare rutrum, urna risus pretium ante, in iaculis metus sapien ac nisl. Mauris vitae mauris tristique, sagittis libero.</p></div></div>
      </div>
    </div>
  </div>
</section>
</main>

<section class="newsletter">
  <div class="wrap">
    <h2><svg width="20" height="15" viewBox="0 0 20 15"><rect x="0" y="0" width="20" height="15" rx="1.5" fill="#fff"/><path d="M1 1.5l9 7 9-7" fill="none" stroke="#333" stroke-width="1.6"/></svg>Newsletter Subscribe</h2>
    <div class="nl-form"><div class="nl-input">Email Address</div><div class="nl-btn">Subscribe</div></div>
  </div>
</section>

<footer>
  <div class="wrap footer-cols">
    <div class="fcol"><h4>News</h4><ul><li>Aliquam vestibulum</li><li>Cras scelerisque</li><li>Aenean</li><li>Duis aneque</li><li>Maecenas ornare</li><li>Proin faucibus</li></ul></div>
    <div class="fcol"><h4>Business</h4><ul><li>Aliquam vestibulum</li><li>Cras scelerisque</li><li>Aenean</li><li>Duis aneque</li><li>Maecenas ornare</li><li>Proin faucibus</li></ul></div>
    <div class="fcol"><h4>Tech</h4><ul><li>Aliquam vestibulum</li><li>Cras scelerisque</li><li>Aenean</li><li>Duis aneque</li><li>Maecenas ornare</li><li>Proin faucibus</li></ul></div>
    <div class="fcol"><h4>Mauris vitae</h4><ul><li>Aliquam vestibulum</li><li>Cras scelerisque</li><li>Aenean</li><li>Duis aneque</li><li>Maecenas ornare</li><li>Proin faucibus</li></ul></div>
    <div class="fcol"><h4>Integer laoreet</h4><ul><li>Aliquam vestibulum</li><li>Cras scelerisque</li><li>Aenean</li><li>Duis aneque</li><li>Maecenas ornare</li><li>Proin faucibus</li></ul></div>
  </div>
  <div class="footer-bottom">
    <div class="wrap">
      <span>Copyright &copy; 2017 Harlow News. All rights reserved.</span>
      <div class="social" aria-label="Social links"><span></span><span></span><span></span><span></span><span></span></div>
    </div>
  </div>
</footer>

</body>
</html>
```